Website to design and sell sundials: www.gnomonvale.com

We have a website that creates a free paper sundial, we want to migrate from this not profit free website to a website where we will continue offering the free paper sundial model but We will also offer a manufactured sundial and sell it.
In order to understand the project, please visit:
http://www.gnomonvale.com/vertical/sundial.html and
http://www.torvel.net/landing/

The website user journey should be redesigned, including the phases that are,
select language
Show product give info
Creation/edit sundial (could be one or more phases)
View created sundial
Buy sundial.

May some of them could be combined or splitted, what It have more sense.

Requirements
Must have
• A description page user journey offering freemium paper sundial and physical sundial to sell.
• A sundial creation page for "free" paper sundial
• A result page for paper sundial
• A sell page for physical

```html
<!DOCTYPE html>
<html lang="en">
<head>
<meta charset="utf-8">
<title>GnomonVale – Create your vertical sundial</title>
<link href="https://fonts.googleapis.com/css2?family=Roboto:wght@300;400;500&display=swap" rel="stylesheet">
<style>
:root{
  --red:#c0312c;
  --red-dark:#a5201d;
  --orange:#f8ad38;
  --nav-top:#f7b230;
  --nav-bottom:#e2931a;
  --dark:#333333;
  --grey-bg:#ebebeb;
  --text:#555555;
  --white:#ffffff;
  --black:#1a1a1a;
}
*{box-sizing:border-box;margin:0;padding:0}
html,body{width:912px;height:1200px;overflow:hidden;background:var(--white)}
body{position:relative;font-family:'Roboto',sans-serif;color:var(--text)}
.abs{position:absolute}
.top-strip{left:0;top:0;width:912px;height:6px;background:var(--red)}
.site-header{left:0;top:6px;width:912px;height:86px;background:var(--white)}
.brand{left:77px;top:33px;display:flex;align-items:center;gap:8px;font-size:21px;font-weight:500;color:var(--red)}
.brand-dot{width:14px;height:14px;border-radius:50%;background:var(--red)}
.phone{left:588px;top:35px;display:flex;align-items:center;gap:10px;font-size:17px;font-weight:300;color:#666}
.lang{left:743px;top:29px;width:101px;height:32px;border:1px solid #333;display:flex;align-items:center;padding-left:12px;gap:6px;font-size:13px;color:#333}
.flag{width:23px;height:14px;background:repeating-linear-gradient(var(--red) 0 2px,#fff 2px 4px);position:relative}
.flag::before{content:"";position:absolute;left:0;top:0;width:10px;height:8px;background:#2b3f8c}
.main-nav{left:0;top:92px;width:912px;height:55px;background:linear-gradient(var(--nav-top),var(--nav-bottom))}
.main-nav a{position:absolute;top:0;height:55px;line-height:55px;font-size:12.5px;color:var(--white);text-decoration:none}
.main-nav a.active{left:65px;width:85px;text-align:center;background:var(--red-dark)}
.hero{left:0;top:147px;width:912px;height:108px;background:var(--dark);color:var(--white);text-align:center;font-size:27px;font-weight:500;line-height:108px}
.location{left:0;top:255px;width:912px;height:361px;background:var(--grey-bg)}
.map{left:63px;top:316px;width:368px;height:254px;border:3px solid #fff;box-shadow:0 0 3px rgba(0,0,0,.25);background:linear-gradient(135deg,#2c4a86 0%,#3a5c9a 35%,#8a8a5a 55%,#b5926a 65%,#2f4f8c 100%)}
h2.red{color:var(--red);font-size:21px;font-weight:400}
.loc-title{left:462px;top:318px}
.loc-text{left:462px;top:350px;width:400px;font-size:8.6px;line-height:18px}
.search{left:462px;top:400px;width:343px;height:29px;background:#fff;border:1px solid #ddd}
.go{left:805px;top:400px;width:37px;height:29px;background:var(--red);color:#fff;font-size:16px;text-align:center;line-height:29px}
.coord{top:450px;font-size:10px;color:#444;display:flex;align-items:center;gap:6px}
.coord span.box{display:inline-block;width:62px;height:20px;background:#fff;border:1px solid #ddd;font-size:9px;line-height:20px;padding-left:7px}
.face-title{left:460px;top:493px;font-size:14px;color:#333}
.face-text{left:458px;top:516px;width:400px;font-size:8.6px;line-height:16.5px}
.options{left:0;top:616px;width:912px;height:357px;background:var(--orange)}
.opt-title{left:66px;top:668px;font-size:20px;color:#fff;font-weight:400}
.lbl{font-size:13px;color:#fff;display:flex;align-items:center;gap:6px}
.radio{display:inline-block;width:13px;height:13px;border:1px solid #fff;border-radius:50%;position:relative}
.radio.on::after{content:"";position:absolute;left:4px;top:4px;width:3px;height:3px;border-radius:50%;background:#fff}
.field{background:#fff}
.tz{left:138px;top:813px;width:228px;height:30px;font-size:10px;color:#333;line-height:30px;padding-left:12px;word-spacing:10px}
.btn{left:66px;top:901px;width:105px;height:33px;background:var(--red);color:#fff;font-size:13.5px;text-align:center;line-height:33px;border-radius:2px}
.card{top:664px;width:223px;height:215px;background:#fff;text-align:center;font-size:10px;color:#444}
.card .photo{height:171px}
.card p{margin-top:7px}
.card .radio{border-color:#444;margin-top:5px}
.footer{left:0;top:973px;width:912px;height:168px;background:var(--red);color:#fff}
.f-head{top:1002px;font-size:12px;font-weight:500;color:#fff}
.f-list{left:75px;top:1030px;list-style:none;font-size:9.2px;line-height:18.6px;color:#fff}
.f-list li::before{content:"▸ ";font-size:7px}
.f-copy{left:236px;top:1030px;width:191px;font-size:9.2px;line-height:12.9px;text-align:justify;color:#fff}
.f-contact{left:494px;top:1030px;font-size:9.2px;line-height:17px;color:#fff}
.f-news{left:690px;top:1030px;width:155px;font-size:9.2px;line-height:12px;color:#fff}
.mail{left:690px;top:1061px;width:112px;height:23px;background:#fff;color:#777;font-size:8.6px;line-height:23px;padding-left:10px}
.submit{left:802px;top:1061px;width:42px;height:23px;background:#e19a1e;color:#fff;font-size:8px;text-align:center;line-height:23px}
.social{top:1098px;width:25px;height:25px;border:1px solid #fff;border-radius:50%}
.bottom{left:0;top:1141px;width:912px;height:59px;background:var(--black);color:#fff;font-size:8.6px;text-align:center;line-height:50px}
</style>
</head>
<body>
<div class="abs top-strip"></div>
<header class="abs site-header"></header>
<div class="abs brand"><span class="brand-dot"></span>GnomonVale.com</div>
<div class="abs phone">
  <svg width="15" height="15" viewBox="0 0 24 24"><path fill="#c0312c" d="M6.6 10.8a15 15 0 0 0 6.6 6.6l2.2-2.2c.3-.3.7-.4 1-.2 1.1.4 2.3.6 3.6.6.6 0 1 .4 1 1V20c0 .6-.4 1-1 1A17 17 0 0 1 3 4c0-.6.4-1 1-1h3.5c.6 0 1 .4 1 1 0 1.3.2 2.5.6 3.6.1.3 0 .7-.2 1z"/></svg>
  (555)014-2207
</div>
<div class="abs lang"><span class="flag"></span>English ⌄</div>

<nav class="abs main-nav">
  <a class="active" href="#">HOME</a>
  <a style="left:168px" href="#">ABOUT US</a>
  <a style="left:270px" href="#">OUR SERVICES</a>
  <a style="left:398px" href="#">PRODUCTS</a>
  <a style="left:507px" href="#">BLOG</a>
  <a style="left:582px" href="#">NEWS</a>
  <a style="left:660px" href="#">LOCATION</a>
  <a style="left:762px" href="#">CONTACT</a>
</nav>

<h1 class="abs hero" style="font-weight:500">CREATE YOUR VERTICAL SUNDIAL</h1>

<section class="abs location"></section>
<div class="abs map" role="img" aria-label="Interactive satellite map for choosing the sundial location"></div>
<h2 class="abs red loc-title">SUNDIAL LOCATION</h2>
<p class="abs loc-text">Select the location where you want to place your paper sundial, mark a line along building wall where you want to put it. Write your address and press Go! (e.g. Picadilly circus, london, UK)</p>
<div class="abs search"></div>
<div class="abs go">Go</div>
<div class="abs coord" style="left:461px">Longitude :<span class="box">0</span></div>
<div class="abs coord" style="left:587px">Latitude :<span class="box">0</span></div>
<div class="abs coord" style="left:708px">Wall declination :<span class="box" style="width:55px">0</span></div>
<h3 class="abs face-title" style="font-weight:400">Now select the face of the building</h3>
<p class="abs face-text">Lorem Ipsum has been the industry's standard dummy text ever since the 1500s, when an unknown printer took a galley of type and scrambled it to make a type specimen book. It has survived not only five centuries, but also the leap into electronic typesetting,</p>

<section class="abs options"></section>
<h2 class="abs opt-title">SUNDIAL OPTIONS</h2>
<div class="abs lbl" style="left:65px;top:723px">Banner :</div>
<div class="abs field" style="left:123px;top:718px;width:243px;height:30px"></div>
<div class="abs lbl" style="left:65px;top:766px">Solar Time :<span class="radio"></span></div>
<div class="abs lbl" style="left:187px;top:766px">Civil Time :<span class="radio on"></span></div>
<div class="abs lbl" style="left:65px;top:820px">Timezone :</div>
<div class="abs field tz">GMT-11) Midway&nbsp;Islands,&nbsp;Samoa)</div>
<div class="abs lbl" style="left:65px;top:864px">Daylight Saving Time :<span class="radio"></span></div>
<div class="abs lbl" style="left:231px;top:864px">Equation of time :<span class="radio"></span></div>
<div class="abs btn">Create sundial</div>

<div class="abs card" style="left:392px">
  <div class="photo" role="img" aria-label="Paper sundial fixed on a brick wall" style="background:linear-gradient(90deg,#4a5a6a 0%,#9b4c3a 25%,#a8553f 60%,#8f4535 100%)"></div>
  <p>Wall sundial</p><span class="radio"></span>
</div>
<div class="abs card" style="left:623px">
  <div class="photo" role="img" aria-label="Paper sundial taped to a window overlooking a terrace" style="background:linear-gradient(180deg,#dfe7ee 0%,#c9cfd2 45%,#8a7a68 75%,#6a5a48 100%)"></div>
  <p>Window sundial</p><span class="radio"></span>
</div>

<footer class="abs footer"></footer>
<h4 class="abs f-head" style="left:75px">LINKS</h4>
<ul class="abs f-list">
  <li>Customer Support</li><li>Documentation</li><li>Resources</li><li>General FAQs</li><li>Shortcodes</li>
</ul>
<h4 class="abs f-head" style="left:236px">NEQUE PORRO QUISQUAM</h4>
<p class="abs f-copy">Lorem Ipsum has been the industry's standard dummy text ever since the 1500s, when an unknown printer took a galley of type and scrambled it to make a type specimen book. It has survived not only five centuries, but also the leap into electronic typesetting, remaining</p>
<h4 class="abs f-head" style="left:494px">GET IN TOUCH</h4>
<div class="abs f-contact">Address : 27 Larchmere Ave, Kelbrook,<br>Ontario K9P4L2<br><span style="display:block;height:5px"></span>Phone : 1 555 019-3346<br><span style="display:block;height:5px"></span>Email : hello@gnomonvale.com</div>
<h4 class="abs f-head" style="left:690px">NEWSLETTER</h4>
<p class="abs f-news">Your about us information would fit here nicely.</p>
<div class="abs mail">Email address</div>
<div class="abs submit">Submit</div>
<div class="abs social" style="left:690px"></div>
<div class="abs social" style="left:727px"></div>
<div class="abs social" style="left:764px"></div>

<div class="abs bottom">Copyright © 2016. All Rights Reserved</div>
</body>
</html>
```